Banner to be displayed at local Farmers Market Booth.

Graphic Design Brief: Farmers Market Banner Contest

Project Overview:We are seeking talented graphic designers to create a visually appealing banner for our booth at the local farmers market. Our company specializes in healthy, all-natural dog and cat treats, and we want a banner that captures our brand identity while drawing in pet owners who value quality and nutrition for their furry friends.

Banner Specifications:

Size: 24 inches x 60 inches (Horizontal orientation) 24" High X 60 wide

Theme: Vintage/Retro

Style: Warm, inviting, nostalgic with a touch of rustic charm

Colors: Earthy, muted tones such as warm browns, soft greens, and creamy yellows. Pops of red or blue may be used sparingly for accents. OR Black and White with gray scales. Would like to see both

Typography: Retro-style fonts that are readable and align with the vintage aesthetic.

Key Elements to Include: website (www.moltbyfarms.com)

Company Name: Moltby Farms

Tagline: " Simply Honest Bites "
Imagery: Illustrations or stylized graphics of happy dogs and cats, possibly interacting with treats.

Emphasis on Natural Ingredients: Icons or design elements that subtly suggest freshness and quality (e.g., leaves, wheat, bones, or paw prints).

Farmers Market Appeal: A design that blends well with the artisanal, handmade, and farm-fresh atmosphere of the market.

Design Considerations:

The banner should be easily readable from a distance.

A balanced composition that doesn't feel overcrowded.

Should evoke trust and warmth while maintaining a professional look.

Avoid overly modern or sleek elements that don’t align with the vintage aesthetic.

Submission Requirements:

High-resolution digital file in PDF or AI format.

CMYK color mode for printing purposes.

Must include a mockup or preview of how it would look in a real farmers market setting.

We look forward to seeing your creative interpretations of our brand! If you have any questions, feel free to reach out.

Font styles to use
Other font styles liked:
• See attachement

Requirements
Nice to have
• Retro/Vintage,playful BUT NOT whimsical

```html
<!DOCTYPE html>
<html lang="en">
<head>
<meta charset="utf-8">
<title>Moltby Farms – Market Banner</title>
<link rel="stylesheet" href="https://fonts.googleapis.com/css2?family=Black+Ops+One&family=Cinzel:wght@400;700;900&display=swap">
<style>
  :root {
    --page: #e8e8e4;
    --ink: #151515;
    --cream: #f2eee4;
    --orange: #e98a3c;
    --orange-edge: #c9551f;
    --art-light: #d9d9d6;
    --art-dark: #5e5e5c;
  }
  html, body {
    margin: 0;
    width: 1200px;
    height: 944px;
    overflow: hidden;
    background: var(--page);
  }
  .banner {
    position: absolute;
    left: 20px;
    top: 245px;
    width: 1160px;
    height: 454px;
    overflow: hidden;
  }
  .banner-shapes {
    position: absolute;
    inset: 0;
  }
  .headline {
    position: absolute;
    right: 488px;
    top: 86px;
    margin: 0;
    font-family: "Black Ops One", sans-serif;
    font-weight: 400;
    font-size: 64px;
    line-height: 68px;
    color: var(--cream);
    text-align: right;
    letter-spacing: 1px;
  }
  .website {
    position: absolute;
    left: 70px;
    width: 602px;
    top: 242px;
    margin: 0;
    font-family: "Cinzel", serif;
    font-size: 26px;
    letter-spacing: 4px;
    color: var(--cream);
    text-align: center;
  }
  .company-name {
    position: absolute;
    left: 26px;
    top: 338px;
    margin: 0;
    font-family: "Cinzel", serif;
    font-weight: 900;
    font-size: 48px;
    letter-spacing: 3px;
    color: var(--ink);
  }
  .tagline {
    position: absolute;
    left: 28px;
    top: 400px;
    margin: 0;
    font-family: "Cinzel", serif;
    font-weight: 700;
    font-size: 33px;
    color: var(--cream);
    white-space: nowrap;
  }
  .brand-mark {
    position: absolute;
    right: 30px;
    top: 36px;
    display: flex;
    align-items: center;
    gap: 8px;
    font-family: "Cinzel", serif;
    font-weight: 700;
    font-size: 24px;
    color: var(--cream);
  }
  .brand-mark .dot {
    width: 14px;
    height: 14px;
    border-radius: 50%;
    background: var(--cream);
  }
</style>
</head>
<body>
  <div class="banner">
    <svg class="banner-shapes" width="1160" height="454" viewBox="0 0 1160 454">
      <defs>
        <linearGradient id="pet-art-tone" x1="0" y1="0" x2="1" y2="1">
          <stop offset="0" stop-color="var(--art-light)"/>
          <stop offset="1" stop-color="var(--art-dark)"/>
        </linearGradient>
      </defs>
      <rect class="orange-field" x="0" y="0" width="1160" height="454" fill="var(--orange)"/>
      <path class="black-field" fill="var(--ink)"
        d="M0 0 H1160 V300 L1100 296 L1060 304 L1000 298 L940 306 L880 300 L820 306
           L770 294 L730 300 L700 286 L672 300 L640 272 L612 292 L585 266 L560 292
           L530 284 L505 296 L480 268 L452 292 L420 284 L392 298 L360 276 L330 296
           L296 280 L262 300 L228 290 L196 300 L160 280 L128 298 L96 290 L62 300
           L30 292 L0 298 Z"/>
      <rect class="bottom-edge" x="0" y="446" width="1160" height="8" fill="var(--orange-edge)"/>
      <rect class="pet-illustration" x="692" y="60" width="442" height="276" rx="6"
        fill="url(#pet-art-tone)" role="img"
        aria-label="Black and white drawing of a dog and a tabby cat lying side by side"/>
    </svg>

    <h1 class="headline">SIMPLY HONEST<br>BITES</h1>
    <p class="website">WWW.MOLTBYFARMS.COM</p>

    <div class="brand-mark"><span class="dot"></span>Moltby</div>

    <h2 class="company-name">MOLTBY FARMS</h2>
    <p class="tagline">PURVEYORS OF PREMIUM PET FOOD &amp; TREATS</p>
  </div>
</body>
</html>
```